Local Flower Farm Needs Business Card Design

I need business cards designed for a flower farm based in Eudora, Kansas.
Business Info:
We are a local cut flower farm located in Eudora, Kansas, founded by Corinne Haldwick. What started as a passion for agriculture and search for more joy in daily life has blossomed into a small business dedicated to providing the community with beautiful, fresh, and sustainable flowers. We specialize in local, seasonal blooms, ensuring that every petal reflects the care and dedication we pour into our craft. Our mission is to deliver the highest quality flowers directly to our customers through local farmers markets and to florists who share our commitment to sustainability. Join us in celebrating the beauty of nature, one bloom at a time!
Contact Details:
Corinne Haldwick
Owner
Phone 913-555-0147
Facebook: Rosalind Thorpe Gardens
Instagram: @RosalindThorpeGardens
Website: RosalindThorpeGardens.example
Target Market(s)
Wholesale to Florists and Direct to Consumer via Farmers Market
Industry/Entity Type
Florist, Farm
Contact Information for Business Card
Name, Contact Info, Logo
Look and feel
Each slider illustrates characteristics of the customer's brand and the style your logo design should communicate.

```html
<!DOCTYPE html>
<html lang="en">
<head>
<meta charset="utf-8">
<title>Rosalind Thorpe Gardens – Business Card</title>
<link rel="stylesheet" href="https://fonts.googleapis.com/css2?family=EB+Garamond:wght@400;500&family=Libre+Baskerville:wght@700&display=swap">
<style>
  :root {
    --backdrop: #2b2b2d;
    --card: #0c2629;
    --ink: #f4f1ea;
    --ink-soft: #d9d6cf;
    --rule: rgba(244, 241, 234, 0.55);
  }
  * { margin: 0; padding: 0; box-sizing: border-box; }
  html, body {
    width: 1200px;
    height: 689px;
    overflow: hidden;
    background: var(--backdrop);
  }
  .stage {
    width: 1200px;
    height: 689px;
    display: flex;
    align-items: center;
    justify-content: center;
    gap: 40px;
  }
  .card {
    width: 540px;
    height: 309px;
    background: var(--card);
    border-radius: 22px;
    position: relative;
    color: var(--ink);
    box-shadow: 0 18px 40px rgba(0, 0, 0, 0.45);
  }
  .seal {
    position: absolute;
    border: 1px solid var(--rule);
    border-radius: 50%;
    display: flex;
    align-items: center;
    justify-content: center;
    text-align: center;
    font-family: "EB Garamond", serif;
    font-weight: 400;
    text-transform: uppercase;
    color: var(--ink);
    line-height: 1.35;
  }
  .card--front .seal {
    width: 220px;
    height: 220px;
    left: 160px;
    top: 44px;
    font-size: 22px;
    letter-spacing: 0.14em;
  }
  .card--back .seal {
    width: 150px;
    height: 150px;
    left: 52px;
    top: 80px;
    font-size: 15px;
    letter-spacing: 0.12em;
  }
  .divider {
    position: absolute;
    left: 232px;
    top: 64px;
    width: 1px;
    height: 182px;
    background: var(--rule);
  }
  .details {
    position: absolute;
    left: 256px;
    top: 70px;
    font-family: "EB Garamond", serif;
  }
  .details__name {
    font-family: "Libre Baskerville", serif;
    font-weight: 700;
    font-size: 23px;
    letter-spacing: 0.01em;
  }
  .details__role {
    font-size: 15px;
    color: var(--ink-soft);
    margin: 4px 0 14px;
  }
  .contact {
    list-style: none;
  }
  .contact li {
    display: flex;
    align-items: center;
    gap: 9px;
    font-size: 16px;
    line-height: 1;
    margin-bottom: 9px;
  }
  .contact svg {
    width: 14px;
    height: 14px;
    flex: none;
  }
  .marker {
    width: 13px;
    height: 13px;
    flex: none;
    border: 1.2px solid var(--ink);
  }
  .marker--square { border-radius: 2px; }
  .marker--circle { border-radius: 50%; }
</style>
</head>
<body>
<main class="stage">
  <section class="card card--front" aria-label="Card front">
    <div class="seal">Rosalind<br>Thorpe<br>Gardens</div>
  </section>

  <section class="card card--back" aria-label="Card back">
    <div class="seal">Rosalind<br>Thorpe<br>Gardens</div>
    <div class="divider"></div>
    <div class="details">
      <h1 class="details__name">Corinne Haldwick</h1>
      <p class="details__role">Owner</p>
      <ul class="contact">
        <li>
          <svg viewBox="0 0 24 24" aria-hidden="true"><path fill="#f4f1ea" d="M6.6 10.8a15.1 15.1 0 0 0 6.6 6.6l2.2-2.2c.3-.3.7-.4 1-.2 1.1.4 2.3.6 3.6.6.6 0 1 .4 1 1V20c0 .6-.4 1-1 1A17 17 0 0 1 3 4c0-.6.4-1 1-1h3.5c.6 0 1 .4 1 1 0 1.3.2 2.5.6 3.6.1.3 0 .7-.2 1z"/></svg>
          913-555-0147
        </li>
        <li><span class="marker marker--square" aria-hidden="true"></span>Rosalind Thorpe Gardens</li>
        <li><span class="marker marker--circle" aria-hidden="true"></span>@RosalindThorpeGardens</li>
        <li>
          <svg viewBox="0 0 24 24" aria-hidden="true" fill="none" stroke="#f4f1ea" stroke-width="1.8"><circle cx="12" cy="12" r="9.5"/><ellipse cx="12" cy="12" rx="4" ry="9.5"/><path d="M2.5 12h19"/></svg>
          RosalindThorpeGardens.example
        </li>
      </ul>
    </div>
  </section>
</main>
</body>
</html>
```